Design a compelling Tarnwove Business Card that will drive people to my site

I want a business card that I can give to people—less to tell them who I am and more to direct them to my website. My website is a portal for Pelmor Aquatics Officials and a place for people who want to become Pelmor Aquatics Officials.
I am uploading my official company logo as well as a business card mockup that I did on my own. Please feel free to completely stray from this design.
I've included a screen recording of the homepage of my website as well.
Target Market(s)
Pelmor Aquatics Officials and people who desire to become one
Contact Information for Business Card
website url
Look and feel
Each slider illustrates characteristics of the customer's brand and the style your logo design should communicate.

```html
<!DOCTYPE html>
<html lang="en">
<head>
<meta charset="utf-8">
<title>Tarnwove Business Card</title>
<link rel="stylesheet" href="https://fonts.googleapis.com/css2?family=Poppins:wght@400;600;700&family=Roboto:wght@400&display=swap">
<style>
  :root {
    --navy: #2b4286;
    --royal: #3552a8;
    --pale: #c9d5f0;
    --ink: #2a2a2a;
    --rule: #4a4a4a;
    --paper: #ffffff;
    --backdrop: #e6e7ea;
  }
  * { box-sizing: border-box; margin: 0; padding: 0; }
  html, body {
    width: 1200px; height: 880px; overflow: hidden;
    background: var(--backdrop);
    font-family: "Poppins", sans-serif;
  }
  .stage { position: relative; width: 1200px; height: 880px; }
  .card {
    position: absolute; left: 250px; width: 700px; height: 400px;
    border-radius: 28px; overflow: hidden;
    box-shadow: 0 12px 30px rgba(0,0,0,.18);
  }
  .card-front { top: 30px; background: var(--navy); color: var(--paper); }
  .card-back { top: 455px; background: var(--paper); }

  .front-wordmark {
    position: absolute; left: 0; right: 0; top: 120px; text-align: center;
    font-weight: 700; font-size: 104px; letter-spacing: -2px; line-height: 1;
  }
  .front-tagline {
    position: absolute; left: 0; right: 0; top: 262px; text-align: center;
    font-weight: 600; font-size: 27px; letter-spacing: .5px;
  }

  .back-wordmark {
    position: absolute; left: 60px; top: 64px;
    font-weight: 700; font-size: 76px; letter-spacing: -2px; line-height: 1;
    color: var(--royal);
  }
  .back-watermark {
    position: absolute; right: 50px; top: 160px;
    font-weight: 700; font-size: 58px; letter-spacing: -1px; line-height: 1;
    color: var(--pale); opacity: .6;
  }
  .accent-bar {
    position: absolute; left: 0; top: 250px; width: 14px; height: 54px;
    background: var(--royal);
  }
  .holder { position: absolute; left: 60px; top: 234px; }
  .holder-name { font-weight: 700; font-size: 30px; color: var(--royal); line-height: 1.1; }
  .holder-title { font-family: "Roboto", sans-serif; font-size: 20px; color: var(--ink); margin-top: 4px; }
  .divider {
    position: absolute; left: 60px; right: 50px; top: 312px;
    height: 1.5px; background: var(--rule);
  }
  .contact {
    position: absolute; top: 330px; display: flex; align-items: center; gap: 10px;
    font-family: "Roboto", sans-serif; font-size: 21px; color: var(--ink);
  }
  .contact-phone { left: 60px; }
  .contact-email { right: 50px; }
  .contact svg { width: 22px; height: 22px; fill: var(--royal); }
</style>
</head>
<body>
<main class="stage">
  <section class="card card-front" aria-label="Card front">
    <div class="front-wordmark">Tarnwove</div>
    <p class="front-tagline">The Poolside Referee's Hub</p>
  </section>

  <section class="card card-back" aria-label="Card back">
    <div class="back-watermark" aria-hidden="true">Tarnwove</div>
    <div class="back-wordmark">Tarnwove</div>
    <span class="accent-bar"></span>
    <div class="holder">
      <p class="holder-name">Marcus Delvane</p>
      <p class="holder-title">CEO &amp; Founder</p>
    </div>
    <span class="divider"></span>
    <p class="contact contact-phone">
      <svg viewBox="0 0 24 24" aria-hidden="true"><path d="M6.6 10.8a15 15 0 0 0 6.6 6.6l2.2-2.2c.3-.3.7-.4 1-.2 1.1.4 2.3.6 3.6.6.6 0 1 .4 1 1V20c0 .6-.4 1-1 1A17 17 0 0 1 3 4c0-.6.4-1 1-1h3.5c.6 0 1 .4 1 1 0 1.3.2 2.5.6 3.6.1.3 0 .7-.2 1z"/></svg>
      (555) 214-7730
    </p>
    <p class="contact contact-email">
      <svg viewBox="0 0 24 24" aria-hidden="true"><path d="M2 5h20v14H2z M2 5l10 8 10-8" fill="none" stroke="#3552a8" stroke-width="2.2"/></svg>
      marcus@tarnwove.com
    </p>
  </section>
</main>
</body>
</html>
```